Fashion-Doll Website

I'm looking to create a new and better website for my growing fashion-doll brand, QUELLIE.

About me: I'm a Brooklyn-based artist, illustrator, and doll-maker and QUELLIE is the name of my doll. Quellie is a character doll (one girl) but she's not necessarily defined by any particular physical trait outside of the sculpt of the doll and her unique sense of style. For example, she could have pink hair and freckles or dark skin and green eyes, but she would still be "Quellie."

My partner and I created the current website ourselves using Adobe Muse. While it has served its purpose, we are not professional graphic or web designers, so I'm looking to graduate to a much more sophisticated and streamlined web design. I want the site to feel sweet and homespun but also hip and edgy. Because the site is so image heavy, I think black and white or black and off-white might be the best color palate, but I'm open to seeing other palates. Quellie's signature color is a muted lavender so maybe that could be integrated into the design. Here is the link:

www.QuellieDoll.example

I want the website to feel more like a shop and less like a gallery/info page. I'm now selling one-of-a-kind porcelain dolls, limited-edition resin dolls, face-plate necklaces, paper dolls, custom doll services, and printed Quellie throw pillows. I also need an interface that will allow me to create new categories, update inventory, and post new items easily.

I need to add new sections for press/articles, multiple image galleries (photography, products, illustrations, comics, and fan art), **collaboration projects, and several flash based doll "dress-up" games.

I would prefer a design that I can code/update myself using Adobe Muse. PSD files import into Muse, so I would prefer that you use them. I'm certainly not opposed to other designs, but I would prefer a design I can manage myself.

I'm including some photos and drawings of Quellie that express her look and vibe. I don't want to use these images in the web design necessarily (I think simple is best) but I thought they would be helpful in expressing the kind of girl she is and how I want the site to feel. I want to work with someone who has a clean, refined, yet whimsical aesthetic who can help me create a website that really expresses how special Quellie is.

Reason: I have had a family emergency come up and I can't devote time to this right now so I'm extending the deadline another 10 days.

Target Market(s)

young eccentrics, art collectors, fashion enthusiasts, and adult doll-collectors

Industry/Entity Type

Fashion

Requirements
Must have
• I need the following main categories: Info, Sales, Galleries, Press, and Dress-up. However, I don't necessarily want or expect the layout to be organized like the current website.

INFO:

*About Quellie (the character)

*Doll specifications: 27" porcelain doll, 22" porcelain doll, 22" resin doll, life-size doll (for window display)

*About the artist

SALES:

*Porcelain dolls

*Resin dolls

*Face-plate necklaces

*Pillows

*Custom doll/necklace info and inquiry form

GALLERIES:

*Photographs

*Collaboration projects

*Illustrations/Comics

*Fan Art/Contests

PRESS:

*An inventory of pdf's of articles about Quellie for users to download or view inside a reader online.

DRESS UP:

*Links to two interactive flash based dress-up games (interactive paper dolls)

Nice to have
• I hold online drawing and design contests from time to time so I would love to have a spot on the site reserved to host the rules and results of my contests.

Quellie has a large facebook and Instagram following so links to her social media would also be great.
instagram: @quelliedoll
facebook: fanpagehub.example/quelliedoll

Should not have
• I'm not looking to see anything too girly, too young, or too sexy.
Quellie is not Tessa, Marble Maiden, or Voxxi. She's a sophisticated young girl who is fresh, funky, and free-spirited.

```html
<!DOCTYPE html>
<html lang="en">
<head>
<meta charset="utf-8">
<title>Quellie Dolls</title>
<link href="https://fonts.googleapis.com/css2?family=Delius&family=Josefin+Sans:wght@300&family=PT+Sans:wght@400;700&family=Signika:wght@300;400;600&display=swap" rel="stylesheet">
<style>
:root{
  --page:#f1f0ee;
  --card:#ffffff;
  --line:#e2e1de;
  --ink:#2b2b2b;
  --text:#4a4a4a;
  --muted:#7a7a7a;
  --orange:#e8701a;
  --orange-hi:#ffa53a;
  --orange-lo:#ff7a10;
}
*{box-sizing:border-box;margin:0;padding:0}
html,body{width:1090px;height:1200px;overflow:hidden}
body{background:var(--page);font-family:"PT Sans",sans-serif;color:var(--text);position:relative}
.abs{position:absolute}
.logo{left:93px;top:38px;font-family:"Josefin Sans",sans-serif;font-weight:300;font-size:56px;letter-spacing:4px;color:var(--ink)}
.social{display:flex;gap:10px;font-family:"Signika",sans-serif;font-weight:400;font-size:13px;color:var(--ink)}
.social span{display:flex;align-items:center;gap:5px}
.social i{display:block;width:10px;height:10px;background:var(--ink)}
.social-top{right:92px;top:40px}
.nav{right:91px;top:95px;display:flex;gap:30px;font-family:"Signika",sans-serif;font-weight:300;font-size:14px;color:#444}
.nav .current{color:#111;font-weight:400}
.hero{left:90px;top:140px;width:910px;height:293px;background:#dddbd8;border:1px solid #d2d0cc}
.hero-stage{position:absolute;left:7px;top:7px;width:894px;height:278px;background:linear-gradient(90deg,#1c1011,#2a1a1b 60%,#1a1011);border-radius:3px;overflow:hidden}
.hero-photo{position:absolute;left:0;top:0;width:254px;height:278px;background:linear-gradient(160deg,#4a3a3d,#c8a9b7 45%,#ead8dc 70%,#8d7378)}
.hero-title{position:absolute;left:283px;top:34px;width:340px;font-family:"Signika",sans-serif;font-weight:300;font-size:31px;line-height:38px;color:#f4f0f0}
.hero-sub{position:absolute;left:283px;top:160px;font-family:"Signika",sans-serif;font-weight:300;font-size:20px;color:#a89a9b}
.dots{position:absolute;left:424px;top:252px;display:flex;gap:8px}
.dots i{width:13px;height:13px;border-radius:50%;background:#8b8485}
.dots i.on{background:#fff}
.menu{position:absolute;left:652px;top:22px;width:222px;background:linear-gradient(180deg,var(--orange-hi),var(--orange-lo));border-radius:2px;list-style:none}
.menu li{height:46.5px;display:flex;align-items:center;padding-left:24px;gap:14px;font-family:"Signika",sans-serif;font-weight:400;font-size:18px;color:#fff;border-top:1px solid rgba(190,80,0,.35)}
.menu li:first-child{border-top:none}
.main{left:90px;top:447px;width:910px;height:552px;background:var(--card);border:1px solid var(--line)}
.heading{font-family:"Delius",cursive;font-weight:400;color:var(--orange);font-size:25px;line-height:30px}
.welcome{left:22px;top:22px}
.intro{left:22px;top:66px;width:600px;font-size:12.5px;line-height:23px}
.art-group{left:22px;top:139px;width:206px;height:210px;background:radial-gradient(ellipse at 50% 45%,#c9a49a,#e7d8d2 55%,#fff 80%)}
.copy{left:263px;top:146px;width:358px;font-size:12.3px;line-height:22.7px;text-align:justify}
.divider{left:18px;top:365px;width:603px;height:1px;background:var(--line)}
.view-all{right:288px;top:389px;font-family:"Signika",sans-serif;font-weight:300;font-size:11.5px;color:#333}
.thumb{top:409px;width:188px;height:116px;border:3px solid #ddd;border-radius:2px}
.t1{left:20px;background:linear-gradient(135deg,#a9b6c9,#d9d47b 45%,#efe7dc)}
.t2{left:227px;background:radial-gradient(circle at 50% 50%,#d9bfa8,#f1ebe5 70%)}
.t3{left:433px;background:radial-gradient(circle at 50% 45%,#e7c18e,#e676b9 55%,#2c2a2e)}
.winners-title{left:659px;top:24px;width:230px;text-align:right;font-size:23px}
.winners{left:659px;top:69px;width:230px;height:243px;border:1px solid var(--line);border-radius:3px;background:linear-gradient(#fff,#f6f6f5)}
.winner{position:absolute;left:23px;display:flex;gap:12px}
.winner-photo{width:70px;height:48px;border:2px solid #ddd;background:linear-gradient(135deg,#6f7a66,#c9c2b6)}
.winner-name{font-family:"Signika",sans-serif;font-weight:400;font-size:14px;color:var(--orange);line-height:16px}
.winner-date{font-family:"Signika",sans-serif;font-weight:300;font-size:12px;color:var(--muted);line-height:20px}
.stars{display:flex;gap:2px;margin-top:1px}
.stars i{width:13px;height:13px;background:var(--orange);border-radius:2px;position:relative}
.stars i::after{content:"";position:absolute;left:3px;top:3px;width:7px;height:7px;background:#fff;clip-path:polygon(50% 0,62% 38%,100% 38%,69% 60%,80% 100%,50% 76%,20% 100%,31% 60%,0 38%,38% 38%)}
.stars i.off{background:#888}
.news-title{left:659px;top:327px;width:230px;text-align:center;font-size:23px}
.newsletter{left:659px;top:371px;width:230px;height:154px;background:linear-gradient(#333,#1f1f1f);border-radius:3px}
.field{position:absolute;left:11px;width:210px;height:35px;background:#fff;border-radius:2px;font-family:"Signika",sans-serif;font-weight:300;font-size:13px;color:#777;padding:9px 18px}
.submit{position:absolute;left:147px;top:108px;width:74px;height:33px;background:linear-gradient(#b9b9b9,#7d7d7d);border-radius:2px;font-family:"Signika",sans-serif;font-weight:600;font-size:14px;color:#fff;text-align:center;line-height:33px}
.contest{left:90px;top:1008px;width:910px;height:104px;background:#f7f6f4;border:1px solid var(--line)}
.contest-art{left:38px;top:20px;width:57px;height:62px;border-radius:4px;background:linear-gradient(180deg,#e9b57a,#cfcfcf 60%,#b8b8b8)}
.contest-title{left:117px;top:26px;width:208px;text-align:center;font-family:"Delius",cursive;font-weight:400;font-size:22px;line-height:27px;color:var(--orange)}
.contest-text{left:351px;top:22px;width:366px;font-size:12.5px;line-height:21px}
.participate{left:737px;top:31px;width:144px;height:42px;background:linear-gradient(var(--orange-hi),var(--orange-lo));border-radius:3px;font-family:"Signika",sans-serif;font-weight:600;font-size:15px;color:#fff;text-align:center;line-height:42px}
.footer-links{left:90px;top:1133px;font-family:"Signika",sans-serif;font-weight:300;font-size:13px;color:#333;word-spacing:4px}
.copyright{left:90px;top:1164px;font-family:"Signika",sans-serif;font-weight:300;font-size:12px;color:#333}
.social-bottom{right:90px;top:1152px}
</style>
</head>
<body>
<div class="abs logo">QUELLIE</div>
<div class="abs social social-top"><span><i></i>fanpagehub</span><span><i></i>@quelliedoll</span></div>
<nav class="abs nav"><span class="current">Home</span><span>Info</span><span>Sales</span><span>Galleries</span><span>Press</span><span>Dress Up</span></nav>

<section class="abs hero">
  <div class="hero-stage">
    <div class="hero-photo" role="img" aria-label="Photograph of a porcelain doll with long pink hair"></div>
    <h1 class="hero-title">Quellie is a modern take on the classic European fashion doll.</h1>
    <p class="hero-sub">Handmade in Bushwick, Brooklyn</p>
    <div class="dots"><i class="on"></i><i></i><i></i><i></i></div>
    <ul class="menu">
      <li>&#10132; Dolls</li><li>&#10132; Necklaces</li><li>&#10132; Pillows</li><li>&#10132; Paper Dolls</li><li>&#10132; Accessories</li>
    </ul>
  </div>
</section>

<main class="abs main">
  <h2 class="abs heading welcome">Welcome to Quellie Dolls</h2>
  <p class="abs intro">Each element of Quellie is designed and handcrafted, from the heirloom-quality porcelain to the custom wigs and garments. Her look embodies Brooklyn street-style, Manhattan sophistication, and the classic lines of yesterday. Quellie represents a new chapter in the venerable tradition of boutique doll-making.</p>
  <div class="abs art-group" role="img" aria-label="Photograph of three dolls in colourful dresses"></div>
  <p class="abs copy">Donec sagittis nisi non ante faucibus tempus. Vestibulum id purus id dui venenatis vulputate in eu neque. Quisque quis mauris sit amet dui interdum lobortis. Aenean non leo ac turpis sodales sodales sed id velit. Cras molestie ultrices lectus, vitae luctus nisl. Etiam rutrum dui eu orci elementum, sed porttitor urna consequat. Fusce tristique a lorem vitae congue. Nam eu purus vitae augue lobortis fringilla rutrum a purus. Praesent vitae nibh nec ante consectetur dignissim. Aliquam eleifend facilisis commodo. Sed interdum quam ut erat scelerisque.</p>
  <div class="abs divider"></div>
  <div class="abs view-all">VIEW ALL PRODUCTS &raquo;</div>
  <div class="abs thumb t1" role="img" aria-label="Illustration of a girl reclining among cushions"></div>
  <div class="abs thumb t2" role="img" aria-label="Illustration of a girl with roses in her hair"></div>
  <div class="abs thumb t3" role="img" aria-label="Photograph of a model with a flower crown on a pink background"></div>

  <h2 class="abs heading winners-title">Winners of this Month</h2>
  <div class="abs winners">
    <div class="winner" style="top:23px"><div class="winner-photo" role="img" aria-label="Winning doll photograph"></div><div><div class="winner-name">Mira Vale</div><div class="winner-date">September - 2 - 2013</div><div class="stars"><i></i><i></i><i></i><i></i><i class="off"></i></div></div></div>
    <div class="winner" style="top:99px"><div class="winner-photo" role="img" aria-label="Winning doll photograph on a beach"></div><div><div class="winner-name">Mira Vale</div><div class="winner-date">September - 2 - 2013</div><div class="stars"><i></i><i></i><i></i><i></i><i class="off"></i></div></div></div>
    <div class="winner" style="top:175px"><div class="winner-photo" role="img" aria-label="Winning doll photograph"></div><div><div class="winner-name">Mira Vale</div><div class="winner-date">September - 2 - 2013</div><div class="stars"><i></i><i></i><i></i><i></i><i class="off"></i></div></div></div>
  </div>

  <h2 class="abs heading news-title">Newsletter Sign Up</h2>
  <div class="abs newsletter">
    <div class="field" style="top:13px">Name</div>
    <div class="field" style="top:62px">Email</div>
    <div class="submit">SUBMIT</div>
  </div>
</main>

<section class="abs contest">
  <div class="abs contest-art" role="img" aria-label="Illustration of a cup of coloured pencils"></div>
  <div class="abs contest-title">DRAWING/ DESIGN<br>CONTESTS</div>
  <p class="abs contest-text">Nam nisl velit, lobortis ac dolor non, suscipit blandit diam. Phasellus port titor felis eu turpis consectetur accumsan. Fusce blandit semper leo, quis fringilla eros eleifend eget.</p>
  <div class="abs participate">PARTICIPATE NOW</div>
</section>

<div class="abs footer-links">Home | Info | Sales | Galleries | Press | Dress Up</div>
<div class="abs copyright">Copyright &copy; 2013 Quelliedoll. &nbsp; All rights reserved.</div>
<div class="abs social social-bottom"><span><i></i>fanpagehub</span><span><i></i>@quelliedoll</span></div>
</body>
</html>
```